WebApp for IoT (Vexa lights and Kirra/Brelline)

I am going to create my own dashbord for Quillet Pro (See other examples on https://quillet.example/) But I want it much more flexible and advanced.
One page per room (So I can have an Zanbo in each room with all functions just for that room) and include controls for light (both overall for the room and in an popupwindow all lightbulbs n the room - se more about how its done in Torvald Vexa app on https://www.torvald-vexa.example/en-us/explore-vexa/apps/bridge) aswell as set volume/track for Kirra.

I want the final solution to be "skinable" so I can choose from Blue-CSS to Green-CSS etc, but at this moment I only want ONE color!

I have added an PDF with the functions I am thinking of, but the design is for you to create!

Please have in mind it will be running on Zanbos on the wall, and in the mobile.

For the moment I only want an PSD of the "Room page", "Light popup" and "Sound Popup", but I might contract the winner to get HTML/CSS as second step.

```html
<!DOCTYPE html>
<html lang="en">
<head>
<meta charset="utf-8">
<title>Room Dashboard – Kitchen and Bedroom</title>
<link rel="stylesheet" href="https://fonts.googleapis.com/css2?family=Roboto:wght@400;500&display=swap">
<style>
  :root {
    --page-bg: #e3e3e3;
    --accent: #4670c6;
    --white: #ffffff;
    --ink: #2b2b2b;
    --text-light: #f2f2f2;
    --slider-dark: #5a5a5a;
    --slider-light: #c9c9c9;
    --kitchen-a: #3b3b3d;
    --kitchen-b: #545356;
    --bedroom-a: #35383a;
    --bedroom-b: #4a3f38;
  }
  * { box-sizing: border-box; margin: 0; padding: 0; }
  html, body { width: 1200px; height: 2452px; overflow: hidden; }
  body { background: var(--page-bg); font-family: "Roboto", Arial, sans-serif; position: relative; }

  .room-screen {
    position: absolute; left: 155px; width: 890px; height: 667px; overflow: hidden;
    box-shadow: 0 6px 18px rgba(0,0,0,.25);
  }
  .room-screen--kitchen { top: 523px; }
  .room-screen--bedroom { top: 1262px; }
  .room-photo { position: absolute; inset: 0; }
  .room-screen--kitchen .room-photo { background: linear-gradient(160deg, var(--kitchen-b) 0%, var(--kitchen-a) 55%, #2f2f31 100%); }
  .room-screen--bedroom .room-photo { background: linear-gradient(150deg, #3a4a4a 0%, var(--bedroom-a) 45%, var(--bedroom-b) 100%); }

  .room-select {
    position: absolute; left: 50px; top: 97px; width: 199px; height: 55px; border-radius: 28px;
    background: var(--accent); color: var(--white); font-size: 18px; font-weight: 500;
    display: flex; align-items: center; justify-content: space-between; padding: 0 24px 0 32px;
  }
  .room-select .caret { width: 0; height: 0; border-left: 6px solid transparent; border-right: 6px solid transparent; border-top: 6px solid var(--white); }

  .icon-badge {
    position: absolute; width: 52px; height: 52px; border-radius: 50%; background: var(--white);
    display: flex; align-items: center; justify-content: center;
  }
  .icon-badge svg { width: 30px; height: 30px; }

  .info-block { position: absolute; width: 160px; text-align: center; color: var(--text-light); font-size: 18px; line-height: 24px; }
  .info-block .icon-badge { position: static; margin: 0 auto 8px; }
  .info-weather { left: 408px; top: 99px; }
  .info-clock { left: 704px; top: 99px; }

  .control-label { position: absolute; left: 120px; color: var(--text-light); font-size: 18px; line-height: 24px; white-space: nowrap; }
  .control-row .icon-badge { left: 50px; }

  .toggle {
    position: absolute; left: 208px; width: 64px; height: 24px; border-radius: 12px;
    font-size: 12px; font-weight: 500; display: flex; align-items: center;
  }
  .toggle .knob { width: 18px; height: 18px; border-radius: 50%; flex-shrink: 0; }
  .toggle--on { background: var(--accent); color: var(--white); padding: 0 0 0 3px; }
  .toggle--on .knob { background: var(--white); margin-right: 11px; }
  .toggle--off { background: var(--white); color: var(--ink); padding: 0 3px 0 14px; justify-content: space-between; }
  .toggle--off .knob { background: var(--accent); }

  .slider {
    position: absolute; left: 50px; width: 247px; height: 47px; border-radius: 8px;
    background: linear-gradient(90deg, var(--slider-dark), var(--slider-light));
  }
  .slider--reverse { background: linear-gradient(90deg, var(--slider-light), var(--slider-dark)); }
  .slider .thumb { position: absolute; top: 4px; width: 39px; height: 39px; border-radius: 50%; border: 2px solid var(--white); }
  .slider .glyph { position: absolute; top: 11px; width: 26px; height: 26px; }

  .device-list { position: absolute; left: 683px; }
  .device-pill {
    position: absolute; left: 0; width: 155px; height: 44px; border-radius: 22px; background: var(--white);
    color: var(--ink); font-size: 16px; font-weight: 500; display: flex; align-items: center; padding: 0 4px 0 2px;
  }
  .device-pill .pill-icon {
    flex: 0 0 40px; width: 40px; height: 40px; border-radius: 50%; background: var(--accent);
    display: flex; align-items: center; justify-content: center;
  }
  .device-pill .pill-icon svg { width: 24px; height: 24px; }
  .device-pill .pill-label { flex: 1 1 auto; text-align: center; white-space: nowrap; line-height: 1; }
  .device-pill--active { background: var(--accent); color: var(--white); border: 2px solid var(--white); padding-left: 0; }
</style>
</head>
<body>

<svg width="0" height="0" style="position:absolute">
  <defs>
    <symbol id="i-bulb" viewBox="0 0 32 32">
      <path d="M16 8a7 7 0 0 0-4 12.7V23h8v-2.3A7 7 0 0 0 16 8z" fill="currentColor"/>
      <rect x="12.5" y="24" width="7" height="2" rx="1" fill="currentColor"/>
      <rect x="13.5" y="27" width="5" height="1.6" rx=".8" fill="currentColor"/>
      <g stroke="currentColor" stroke-width="1.6" stroke-linecap="round">
        <path d="M16 2v3M5 14H2M30 14h-3M7.5 5.5l2 2M24.5 5.5l-2 2M6 22l2-1.5M26 22l-2-1.5"/>
      </g>
    </symbol>
    <symbol id="i-thermo" viewBox="0 0 32 32">
      <path d="M13 5a3 3 0 0 1 6 0v13.5a6 6 0 1 1-6 0z" fill="none" stroke="currentColor" stroke-width="1.8"/>
      <circle cx="16" cy="23" r="3.2" fill="currentColor"/><rect x="15" y="11" width="2" height="11" fill="currentColor"/>
      <path d="M21 8h3M21 11h3M21 14h3" stroke="currentColor" stroke-width="1.4"/>
    </symbol>
    <symbol id="i-calendar" viewBox="0 0 32 32">
      <rect x="3" y="6" width="22" height="20" rx="2" fill="none" stroke="currentColor" stroke-width="1.8"/>
      <rect x="3" y="6" width="22" height="5" fill="currentColor"/>
      <path d="M8 3v5M20 3v5" stroke="currentColor" stroke-width="1.8"/>
      <path d="M7 15h3v3H7zM12 15h3v3h-3zM7 20h3v3H7z" fill="currentColor"/>
      <circle cx="23" cy="23" r="6.5" fill="currentColor" stroke="#fff" stroke-width="1.5"/>
      <path d="M23 19.5V23h3" stroke="#fff" stroke-width="1.6" fill="none"/>
    </symbol>
    <symbol id="i-sun" viewBox="0 0 32 32">
      <circle cx="16" cy="16" r="6" fill="currentColor"/>
      <g stroke="currentColor" stroke-width="2" stroke-linecap="round">
        <path d="M16 2v4M16 26v4M2 16h4M26 16h4M6 6l3 3M23 23l3 3M26 6l-3 3M9 23l-3 3"/>
      </g>
    </symbol>
    <symbol id="i-volume" viewBox="0 0 32 32">
      <path d="M5 12h5l7-6v20l-7-6H5z" fill="currentColor"/>
      <path d="M21 11a6 6 0 0 1 0 10M24 8a10 10 0 0 1 0 16" fill="none" stroke="currentColor" stroke-width="2" stroke-linecap="round"/>
    </symbol>
    <symbol id="i-volume-down" viewBox="0 0 32 32">
      <path d="M4 12h5l7-6v20l-7-6H4z" fill="currentColor"/>
      <path d="M20 16h7" stroke="currentColor" stroke-width="2.4"/>
    </symbol>
    <symbol id="i-speaker" viewBox="0 0 32 32">
      <rect x="8" y="3" width="16" height="26" rx="2" fill="none" stroke="currentColor" stroke-width="1.8"/>
      <circle cx="16" cy="9" r="2.4" fill="none" stroke="currentColor" stroke-width="1.6"/>
      <circle cx="16" cy="20" r="5" fill="none" stroke="currentColor" stroke-width="1.6"/>
      <circle cx="16" cy="20" r="1.6" fill="currentColor"/>
    </symbol>
  </defs>
</svg>

<!-- Kitchen room page -->
<section class="room-screen room-screen--kitchen">
  <div class="room-photo" role="img" aria-label="Dimmed photo of a modern kitchen with pendant lamps, dark cabinets and a granite island"></div>

  <div class="room-select">KITCHEN <span class="caret"></span></div>

  <div class="info-block info-weather">
    <div class="icon-badge"><svg style="color:var(--accent)"><use href="#i-thermo"/></svg></div>
    23° SUNNY
  </div>
  <div class="info-block info-clock">
    <div class="icon-badge"><svg style="color:var(--accent)"><use href="#i-calendar"/></svg></div>
    2022-07-14<br>15:23
  </div>

  <div class="control-row">
    <div class="icon-badge" style="top:316px"><svg style="color:var(--accent)"><use href="#i-bulb"/></svg></div>
    <div class="control-label" style="top:330px">LIGHT</div>
    <div class="toggle toggle--on" style="top:330px"><span class="knob"></span>ON</div>
    <div class="slider" style="top:398px">
      <svg class="glyph" style="left:12px;color:var(--white)"><use href="#i-sun"/></svg>
      <span class="thumb" style="right:2px"></span>
    </div>
  </div>

  <div class="device-list">
    <div class="device-pill device-pill--active" style="top:326px"><span class="pill-icon" style="background:var(--white)"><svg style="color:var(--accent)"><use href="#i-bulb"/></svg></span><span class="pill-label">LIGHT 1</span></div>
    <div class="device-pill" style="top:396px"><span class="pill-icon"><svg style="color:var(--white)"><use href="#i-bulb"/></svg></span><span class="pill-label">LIGHT 2</span></div>
    <div class="device-pill" style="top:474px"><span class="pill-icon"><svg style="color:var(--white)"><use href="#i-bulb"/></svg></span><span class="pill-label">LIGHT 3</span></div>
  </div>
</section>

<!-- Bedroom room page -->
<section class="room-screen room-screen--bedroom">
  <div class="room-photo" role="img" aria-label="Dimmed photo of a bedroom with a blossom wall mural, a bed and open wardrobe shelves"></div>

  <div class="room-select">BEDROOM <span class="caret"></span></div>

  <div class="info-block info-weather">
    <div class="icon-badge"><svg style="color:var(--accent)"><use href="#i-thermo"/></svg></div>
    23° SUNNY
  </div>
  <div class="info-block info-clock">
    <div class="icon-badge"><svg style="color:var(--accent)"><use href="#i-calendar"/></svg></div>
    2022-07-14<br>15:23
  </div>

  <div class="control-row">
    <div class="icon-badge" style="top:261px"><svg style="color:var(--accent)"><use href="#i-bulb"/></svg></div>
    <div class="control-label" style="top:275px">LIGHT</div>
    <div class="toggle toggle--off" style="top:275px">OFF<span class="knob"></span></div>
    <div class="slider slider--reverse" style="top:343px">
      <span class="thumb" style="left:2px"></span>
      <svg class="glyph" style="right:10px;color:var(--white)"><use href="#i-sun"/></svg>
    </div>
  </div>

  <div class="control-row">
    <div class="icon-badge" style="top:435px"><svg style="color:var(--accent)"><use href="#i-volume"/></svg></div>
    <div class="control-label" style="top:449px">VOLUME</div>
    <div class="toggle toggle--on" style="top:449px"><span class="knob"></span>ON</div>
    <div class="slider" style="top:517px">
      <svg class="glyph" style="left:8px;color:var(--white)"><use href="#i-volume-down"/></svg>
      <span class="thumb" style="right:2px"></span>
    </div>
  </div>

  <div class="device-list">
    <div class="device-pill device-pill--active" style="top:318px"><span class="pill-icon" style="background:var(--white)"><svg style="color:var(--accent)"><use href="#i-speaker"/></svg></span><span class="pill-label">SPEAKER 1</span></div>
    <div class="device-pill" style="top:391px"><span class="pill-icon"><svg style="color:var(--white)"><use href="#i-speaker"/></svg></span><span class="pill-label">SPEAKER 2</span></div>
    <div class="device-pill" style="top:464px"><span class="pill-icon"><svg style="color:var(--white)"><use href="#i-speaker"/></svg></span><span class="pill-label">SPEAKER 3</span></div>
    <div class="device-pill" style="top:537px"><span class="pill-icon"><svg style="color:var(--white)"><use href="#i-speaker"/></svg></span><span class="pill-label">SPEAKER 4</span></div>
  </div>
</section>

</body>
</html>
```